One business card required with 2 company logos and 2 people's details

One business card required.
No preference on design - One side could show the 2 different business logos for the companies we own. The reverse could have the details shown below.
Another option could be one business one side and one business on the reverse. Happy to receive designs.

Dora Pellham
07700 913 286
Rowena Tindall
07700 958 137

website: quietmeadowbloom.co.uk
email: info@quietmeadowbloom.co.uk

website: brightharbourevents.co.uk
email: info:brightharbourevents.co.uk

May be nice to have icons instead of the words email/website?

I have included different versions of the logos to help with your design.

Contact Information for Business Card

see project overview

Requirements
Must have
• both company logos, both contact names and contact details

```html
<!DOCTYPE html>
<html lang="en">
<head>
<meta charset="utf-8">
<title>Bright Harbour Events &amp; Quiet Meadow Bloom – Business Card</title>
<link rel="stylesheet" href="https://fonts.googleapis.com/css2?family=Cormorant+Garamond:ital,wght@1,600;1,700&family=Jost:wght@300;400;500&family=Roboto:wght@400&display=swap">
<style>
  :root {
    --backdrop: #2b2b2b;
    --card: #ffffff;
    --royal: #4a63d2;
    --royal-deep: #1f4fc8;
    --cyan: #2fd3e0;
    --ink: #111111;
    --logo-blue: #1e6fe0;
    --logo-ink: #3a3560;
    --rule: #6f8fe0;
    --white: #ffffff;
  }
  * { margin: 0; padding: 0; box-sizing: border-box; }
  html, body {
    width: 1125px; height: 1200px; overflow: hidden;
    background: var(--backdrop);
  }
  .canvas { position: relative; width: 1125px; height: 1200px; }

  .card {
    position: absolute; left: 150px; width: 826px; height: 471px;
    background: var(--card); border-radius: 28px; overflow: hidden;
  }
  .card--front { top: 98px; }
  .card--back { top: 631px; }

  /* Front: two company names */
  .brand {
    position: absolute; font-family: "Jost", sans-serif; font-weight: 500;
    text-align: center;
  }
  .brand--events {
    left: 120px; top: 180px; width: 230px;
    color: var(--logo-blue); font-size: 30px; line-height: 1.1; letter-spacing: 2px;
    text-transform: uppercase;
  }
  .brand-divider {
    position: absolute; left: 372px; top: 138px; width: 1px; height: 218px;
    background: var(--rule);
  }
  .brand--bloom {
    left: 420px; top: 120px; width: 230px; height: 230px;
    display: flex; align-items: center; justify-content: center;
  }
  .brand-ring {
    position: absolute; inset: 0; border: 2px solid var(--logo-blue); border-radius: 50%;
  }
  .brand-name {
    position: relative; color: var(--logo-ink); font-size: 30px; line-height: 1.15;
  }

  /* Back: people and contact details */
  .person {
    position: absolute; left: 52px;
    font-family: "Cormorant Garamond", serif; font-style: italic; font-weight: 700;
    font-size: 34px; color: var(--royal); letter-spacing: 0.5px;
  }
  .person--first { top: 44px; }
  .person--second { top: 124px; }
  .phone {
    position: absolute; left: 52px; display: flex; align-items: center; gap: 6px;
    font-family: "Roboto", sans-serif; font-size: 19px; color: var(--ink);
  }
  .phone--first { top: 98px; }
  .phone--second { top: 187px; }
  .phone svg { width: 15px; height: 15px; }

  .wave { position: absolute; left: 0; top: 0; width: 826px; height: 471px; }

  .contacts {
    position: absolute; right: 40px; top: 333px; list-style: none;
    font-family: "Jost", sans-serif; font-weight: 300; font-size: 19px; color: var(--white);
  }
  .contacts li {
    display: flex; justify-content: flex-end; align-items: center; gap: 16px;
    height: 25px;
  }
  .contacts svg { width: 16px; height: 16px; flex: none; }
</style>
</head>
<body>
<main class="canvas">

  <section class="card card--front" aria-label="Card front with both company names">
    <div class="brand brand--events">Bright<br>Harbour<br>Events</div>
    <div class="brand-divider"></div>
    <div class="brand brand--bloom">
      <span class="brand-ring"></span>
      <span class="brand-name">Quiet<br>Meadow<br>Bloom</span>
    </div>
  </section>

  <section class="card card--back" aria-label="Card back with contact details">
    <svg class="wave" viewBox="0 0 826 471" preserveAspectRatio="none" aria-hidden="true">
      <path d="M0,292 C150,372 300,390 430,340 C570,285 690,150 770,158 C800,162 815,175 826,185 L826,471 L0,471 Z" fill="var(--cyan)"/>
      <path d="M0,280 C150,350 300,360 430,320 C570,270 690,135 770,145 C800,150 815,165 826,175 L826,200 C815,190 800,180 772,176 C690,170 575,300 430,352 C300,392 150,382 0,302 Z" fill="var(--royal-deep)" opacity="0.85"/>
      <path d="M0,306 C150,380 300,398 430,350 C570,297 690,168 772,174 C800,177 815,188 826,196" fill="none" stroke="var(--white)" stroke-width="2"/>
      <path d="M0,312 C150,386 300,404 430,356 C570,303 690,176 772,182 C800,185 815,196 826,204 L826,471 L0,471 Z" fill="var(--royal)"/>
    </svg>

    <div class="person person--first">Rowena Tindall</div>
    <div class="phone phone--first">
      <svg viewBox="0 0 24 24" aria-hidden="true"><path fill="var(--cyan)" d="M6.6 10.8a15.1 15.1 0 0 0 6.6 6.6l2.2-2.2a1 1 0 0 1 1-.25 11.4 11.4 0 0 0 3.6.57 1 1 0 0 1 1 1V20a1 1 0 0 1-1 1A17 17 0 0 1 3 4a1 1 0 0 1 1-1h3.5a1 1 0 0 1 1 1c0 1.25.2 2.45.57 3.6a1 1 0 0 1-.25 1z"/></svg>
      <span>07700 958 137</span>
    </div>
    <div class="person person--second">Dora Pellham</div>
    <div class="phone phone--second">
      <svg viewBox="0 0 24 24" aria-hidden="true"><path fill="var(--cyan)" d="M6.6 10.8a15.1 15.1 0 0 0 6.6 6.6l2.2-2.2a1 1 0 0 1 1-.25 11.4 11.4 0 0 0 3.6.57 1 1 0 0 1 1 1V20a1 1 0 0 1-1 1A17 17 0 0 1 3 4a1 1 0 0 1 1-1h3.5a1 1 0 0 1 1 1c0 1.25.2 2.45.57 3.6a1 1 0 0 1-.25 1z"/></svg>
      <span>07700 913 286</span>
    </div>

    <ul class="contacts">
      <li><span>info@quietmeadowbloom.co.uk</span>
        <svg viewBox="0 0 16 16" aria-hidden="true"><rect x="1" y="3" width="14" height="10" fill="var(--cyan)"/><path d="M1 3l7 6 7-6" fill="none" stroke="var(--royal)" stroke-width="1.2"/></svg></li>
      <li><span>quietmeadowbloom.co.uk</span>
        <svg viewBox="0 0 16 16" aria-hidden="true"><circle cx="8" cy="8" r="7" fill="var(--cyan)"/><path d="M1 8h14M8 1c-3 3-3 11 0 14M8 1c3 3 3 11 0 14" fill="none" stroke="var(--royal)" stroke-width="1"/></svg></li>
      <li><span>info:brightharbourevents.co.uk</span>
        <svg viewBox="0 0 16 16" aria-hidden="true"><rect x="1" y="3" width="14" height="10" fill="var(--cyan)"/><path d="M1 3l7 6 7-6" fill="none" stroke="var(--royal)" stroke-width="1.2"/></svg></li>
      <li><span>brightharbourevents.co.uk</span>
        <svg viewBox="0 0 16 16" aria-hidden="true"><circle cx="8" cy="8" r="7" fill="var(--cyan)"/><path d="M1 8h14M8 1c-3 3-3 11 0 14M8 1c3 3 3 11 0 14" fill="none" stroke="var(--royal)" stroke-width="1"/></svg></li>
    </ul>
  </section>

</main>
</body>
</html>
```